Lumavento business card

We need a modern business card - With our 4 colors - See web: www.lumavento.dk

I have attached logo and som old business Cards we have - Lets Make the new ones shine...:-) -

Industry/Entity Type

Business

Requirements
Must have
• the logo with lumavento only,

```html
<!DOCTYPE html>
<html lang="da">
<head>
<meta charset="utf-8">
<title>Lumavento business card</title>
<link href="https://fonts.googleapis.com/css2?family=Questrial&display=swap" rel="stylesheet">
<style>
  :root {
    --backdrop: #3a3b3d;
    --card: #2a2d31;
    --ink: #eceeef;
    --lime: #a3c93a;
    --purple: #7b2a82;
    --magenta: #e5108c;
    --orange: #f3861f;
  }
  * { margin: 0; padding: 0; box-sizing: border-box; }
  html, body {
    width: 1200px; height: 1189px; overflow: hidden;
    background: var(--backdrop);
    font-family: "Questrial", "Helvetica Neue", Arial, sans-serif;
    color: var(--ink);
  }
  .card {
    position: absolute; left: 170px;
    width: 860px; height: 492px;
    background: var(--card);
    border-radius: 22px;
    overflow: hidden;
    box-shadow: 0 14px 30px rgba(0,0,0,.45);
  }
  .card--front { top: 60px; }
  .card--back { top: 636px; }

  .colour-band {
    position: absolute; left: 0; right: 0; bottom: 0; height: 22px;
    display: flex;
  }
  .colour-band span:nth-child(1) { flex: 30; background: var(--purple); }
  .colour-band span:nth-child(2) { flex: 26; background: var(--magenta); }
  .colour-band span:nth-child(3) { flex: 22; background: var(--lime); }
  .colour-band span:nth-child(4) { flex: 22; background: var(--orange); }

  /* front */
  .front-brand {
    position: absolute; left: 0; right: 0; top: 150px; text-align: center;
  }
  .brand-name {
    font-size: 40px; letter-spacing: 9px; color: var(--ink);
  }
  .brand-rule {
    height: 3px; background: var(--lime); margin: 14px auto 0;
  }
  .front-brand .brand-rule { width: 400px; }
  .tagline { font-size: 21px; margin-top: 14px; }
  .front-web {
    position: absolute; left: 0; right: 0; bottom: 88px;
    text-align: center; font-size: 26px; letter-spacing: 1px;
  }

  /* back */
  .back-brand { position: absolute; left: 70px; top: 110px; width: 400px; }
  .back-brand .brand-name { font-size: 38px; text-align: center; }
  .back-brand .brand-rule { width: 400px; }
  .back-brand .tagline { text-align: center; }
  .long-rule {
    position: absolute; left: 70px; right: 190px; top: 262px;
    height: 1.5px; background: var(--lime);
  }
  .social {
    position: absolute; right: 60px; top: 42px; display: flex; gap: 18px;
  }
  .social span {
    width: 34px; height: 34px; border: 2px solid var(--ink); border-radius: 50%;
  }
  .person { position: absolute; right: 60px; top: 200px; text-align: right; }
  .person-name { font-size: 32px; letter-spacing: .5px; }
  .person-role { font-size: 22px; color: var(--lime); margin-top: 2px; }
  .address {
    position: absolute; right: 60px; top: 300px; text-align: right;
    font-size: 25px; line-height: 1.2;
  }
  .contacts {
    position: absolute; left: 70px; top: 300px; list-style: none;
  }
  .contacts li {
    display: flex; align-items: center; gap: 14px;
    font-size: 27px; line-height: 1; margin-bottom: 10px;
  }
  .contact-icon {
    width: 30px; height: 30px; border-radius: 5px; background: var(--lime);
    display: flex; align-items: center; justify-content: center;
  }
</style>
</head>
<body>

<section class="card card--front">
  <div class="front-brand">
    <div class="brand-name">lumavento</div>
    <div class="brand-rule"></div>
    <p class="tagline">Medier til unge</p>
  </div>
  <p class="front-web">www.lumavento.dk</p>
  <div class="colour-band"><span></span><span></span><span></span><span></span></div>
</section>

<section class="card card--back">
  <div class="social" aria-label="Social profiles">
    <span></span><span></span><span></span><span></span>
  </div>

  <div class="back-brand">
    <div class="brand-name">lumavento</div>
    <div class="brand-rule"></div>
    <p class="tagline">Medier til unge</p>
  </div>

  <div class="long-rule"></div>

  <div class="person">
    <p class="person-name">Jonas Ravnholt</p>
    <p class="person-role">Salgsdirektør</p>
  </div>

  <p class="address">Kastanievej 14<br>2000 Lindholm</p>

  <ul class="contacts">
    <li>
      <span class="contact-icon">
        <svg width="18" height="20" viewBox="0 0 18 20"><rect x="4" y="1" width="10" height="18" rx="2" fill="none" stroke="#2a2d31" stroke-width="2"/><circle cx="9" cy="15.5" r="1.3" fill="#2a2d31"/></svg>
      </span>
      +45 20 31 42 53
    </li>
    <li>
      <span class="contact-icon">
        <svg width="20" height="18" viewBox="0 0 20 18"><path d="M2 6c0-3 16-3 16 0v2h-4V6H6v2H2z" fill="#2a2d31"/><rect x="4" y="9" width="12" height="7" rx="1.5" fill="#2a2d31"/></svg>
      </span>
      +45 36 74 19 08
    </li>
    <li>
      <span class="contact-icon">
        <svg width="20" height="16" viewBox="0 0 20 16"><rect x="1.5" y="2" width="17" height="12" fill="none" stroke="#2a2d31" stroke-width="2"/><path d="M1.5 2l8.5 7 8.5-7" fill="none" stroke="#2a2d31" stroke-width="2"/></svg>
      </span>
      jr@lumavento.dk
    </li>
  </ul>

  <div class="colour-band"><span></span><span></span><span></span><span></span></div>
</section>

</body>
</html>
```